Tellmora Corporate Stationery

Look for design of all new corporate stationery for an existing insurance broking business that is going through a redesign and move from older partners to younger family members. New Logo is attached. Company is Brisbane based.
Colours in the Logo is Hex #43bed8 and website features a lot of hex #17b8d8. Website front page "A plan to protect you" - headline. "Professional and Individual advice to protect your greatest assets" - tagline.

Stationery required: Business Cards, Letter head, Thank-you cards, Birthday cards, Presentation folders, With Compliment slips and a powerpoint template. We also would like to send a card to all customers with the something along of the lines of "something new".

Target Market(s)

Customers of Insurance business looking at superannuation, life and income protection insurance, investment advice and wills

Industry/Entity Type

Insurance Broker

Font styles to use
Other font styles liked:
• same as logo

Requirements
Must have
• The above designs for new stationery for the new business including:
• Business Cards, Letter head, Thank-you cards, Birthday cards, Presentation folders, With Compliment slips and a powerpoint template. We also would like to send a card to all customers with the something along of the lines of "something new".
Nice to have
• It is a new look - long time family business being passed to next generation - big focus on advice for YOU, individual advice etc..

```html
<!DOCTYPE html>
<html lang="en">
<head>
<meta charset="utf-8">
<title>Tellmora Financial Group – Business Card</title>
<link rel="stylesheet" href="https://fonts.googleapis.com/css2?family=Open+Sans:wght@400;600;700&display=swap">
<style>
  :root {
    --brand-cyan: #43bed8;
    --brand-cyan-deep: #17b8d8;
    --cyan-light: #7fd6e8;
    --ink: #3c3c3c;
    --ink-soft: #6b6b6b;
    --grey-band: #7a7c80;
    --paper: #ffffff;
    --paper-shade: #e9eaeb;
    --stage: #f1f2f3;
  }
  * { box-sizing: border-box; margin: 0; padding: 0; }
  html, body {
    width: 1200px; height: 843px; overflow: hidden;
    background: var(--stage);
    font-family: "Open Sans", Arial, sans-serif;
  }
  .stage {
    width: 1200px; height: 843px;
    display: flex; align-items: center; justify-content: center; gap: 40px;
  }
  .card {
    position: relative; width: 540px; height: 309px;
    border-radius: 3px; overflow: hidden;
    box-shadow: 0 6px 18px rgba(0,0,0,.18);
  }

  /* Back side */
  .card--back {
    background: linear-gradient(160deg, var(--cyan-light) 0%, var(--brand-cyan) 45%, var(--brand-cyan-deep) 100%);
  }
  .card--back .brand {
    position: absolute; right: 34px; bottom: 58px; text-align: left;
  }
  .card--back .brand-name { color: var(--paper); font-size: 30px; }
  .card--back .brand-sub { color: var(--paper); }
  .card--back .back-web {
    position: absolute; right: 36px; bottom: 30px;
    color: rgba(255,255,255,.85); font-size: 14px; letter-spacing: 3px;
  }

  /* Brand lockup */
  .brand-mark {
    display: flex; align-items: center; gap: 10px;
  }
  .brand-dot {
    width: 26px; height: 26px; border-radius: 50%;
    background: var(--ink-soft);
  }
  .brand-name {
    font-weight: 700; font-size: 32px; letter-spacing: 1px;
    color: var(--brand-cyan); line-height: 1;
  }
  .brand-sub {
    font-weight: 400; font-size: 13px; letter-spacing: 1.5px;
    color: var(--ink-soft); text-transform: uppercase; margin-top: 3px;
  }

  /* Front side */
  .card--front {
    background: linear-gradient(100deg, var(--paper) 0%, var(--paper) 55%, var(--paper-shade) 100%);
  }
  .card--front .brand { position: absolute; left: 30px; top: 22px; }
  .contact {
    position: absolute; left: 30px; top: 116px;
    color: var(--ink); font-size: 13px; line-height: 19px;
  }
  .contact-address { margin-bottom: 2px; }
  .contact-row { display: flex; align-items: center; gap: 8px; }
  .contact-row svg { width: 12px; height: 12px; fill: var(--brand-cyan); flex: none; }
  .person {
    position: absolute; right: 34px; bottom: 56px; text-align: right;
  }
  .person-name {
    font-weight: 700; font-size: 19px; color: var(--brand-cyan); letter-spacing: .5px;
  }
  .person-role { font-size: 14px; color: var(--ink); }
  .footer-band {
    position: absolute; left: 0; right: 0; bottom: 0; height: 34px; display: flex;
  }
  .footer-web {
    flex: 1;
    background: linear-gradient(90deg, var(--brand-cyan) 0%, var(--brand-cyan) 55%, rgba(67,190,216,.35) 100%);
    color: var(--paper); font-size: 13px; letter-spacing: 3px;
    display: flex; align-items: center; padding-left: 30px;
  }
  .footer-end {
    width: 120px; background: var(--grey-band);
    display: flex; align-items: center; padding-left: 14px;
  }
  .footer-end .brand-dot { width: 20px; height: 20px; background: #b9bbbe; }
</style>
</head>
<body>
<main class="stage">

  <section class="card card--back" aria-label="Business card back">
    <div class="brand">
      <div class="brand-name">TELLMORA</div>
      <div class="brand-sub">Financial Group</div>
    </div>
    <div class="back-web">www.tellmora.example</div>
  </section>

  <section class="card card--front" aria-label="Business card front">
    <div class="brand">
      <div class="brand-mark">
        <div>
          <div class="brand-name">TELLMORA</div>
          <div class="brand-sub">Financial Group</div>
        </div>
      </div>
    </div>

    <div class="contact">
      <div class="contact-address">214 Wattlebrook Road<br>Brisbane, Queensland 4000</div>
      <div class="contact-row">
        <svg viewBox="0 0 24 24" aria-hidden="true"><path d="M6.6 10.8a15.2 15.2 0 0 0 6.6 6.6l2.2-2.2a1 1 0 0 1 1-.25 11.4 11.4 0 0 0 3.6.57 1 1 0 0 1 1 1V20a1 1 0 0 1-1 1A17 17 0 0 1 3 4a1 1 0 0 1 1-1h3.5a1 1 0 0 1 1 1c0 1.25.2 2.45.57 3.57a1 1 0 0 1-.25 1z"/></svg>
        <span>07 3184 2205</span>
      </div>
      <div class="contact-row">
        <svg viewBox="0 0 24 24" aria-hidden="true"><path d="M7 1h10a2 2 0 0 1 2 2v18a2 2 0 0 1-2 2H7a2 2 0 0 1-2-2V3a2 2 0 0 1 2-2zm0 3v14h10V4zm5 15.5a1.2 1.2 0 1 0 0 2.4 1.2 1.2 0 0 0 0-2.4z"/></svg>
        <span>0412 578 903</span>
      </div>
      <div class="contact-row">
        <svg viewBox="0 0 24 24" aria-hidden="true"><path d="M6 2h10v5H6zM3 8h18a2 2 0 0 1 2 2v7h-4v5H5v-5H1v-7a2 2 0 0 1 2-2zm4 8v4h10v-4z"/></svg>
        <span>07 3184 2206</span>
      </div>
      <div class="contact-row">
        <svg viewBox="0 0 24 24" aria-hidden="true"><path d="M2 5h20v14H2zm2 2v.5l8 5 8-5V7zm0 2.8V17h16V9.8l-8 5z"/></svg>
        <span>hello@tellmora.example</span>
      </div>
    </div>

    <div class="person">
      <div class="person-name">DANIEL REEVE</div>
      <div class="person-role">CEO/Founder</div>
    </div>

    <div class="footer-band">
      <div class="footer-web">www.tellmora.example</div>
      <div class="footer-end"><div class="brand-dot"></div></div>
    </div>
  </section>

</main>
</body>
</html>
```